Harrow Tavern & Grille Menu Makeover

I am looking for a professional look to update our current menu. We are an independently owned sports bar and grill. Up to this point, I have done all of my own graphic designing. I am looking for something classy/family oriented. We are a very family friendly sports bar that offers a wide variety of menu options. Our website is www.harrowtavernco.example. This may help you get more of a feel for what type of place we are and what we offer. Our menu is listed on the website. My current menu is 8.5x14 inserts that feature a cover page, 4 inside pages and a back page. I would like something a little more condensed than this. Possibly a large tri-fold menu? I am open to all new ideas. I do have some pictures on my menu now, and would like to continue using a few pictures to feature some of my items. I would like something that is in a format that gives me the option to change items and prices on my own in the future. I would also like it to feature, or inform my patrons about our technology that we offer. We offer online ordering and we are a "verified venue" with Brewvoke.( a social site for craft beer lovers).

Industry/Entity Type

Sports Bar

Requirements
Nice to have
• Nice to have some pictures, but does not have to. We do feature 9 different beers on tap. A lot of them are local craft beers from the state of Kansas. Not sure if that is something we can feature, but it is a nice talking point. All of our tables and bar are hand built. With a rich mahogany finish on all of our woodwork, some type of "woodgrain" look into the menu would be nice.

```html
<!DOCTYPE html>
<html lang="en">
<head>
<meta charset="utf-8">
<title>Harrow Tavern &amp; Grille — Menu</title>
<link rel="stylesheet" href="https://fonts.googleapis.com/css2?family=Oswald:wght@300;400&family=Playfair+Display+SC:wght@700&family=Michroma&display=swap">
<style>
:root{
  --mahogany-dark:#3a1208;
  --mahogany:#6e2512;
  --mahogany-light:#8c3a1c;
  --paper:#e6d2a8;
  --paper-light:#efe0bd;
  --paper-edge:#b98c52;
  --ink:#1f1712;
  --ink-soft:#3a2d22;
  --white:#ffffff;
}
*{margin:0;padding:0;box-sizing:border-box}
html,body{width:850px;height:1200px;overflow:hidden}
body{
  position:relative;
  background:
    repeating-linear-gradient(92deg, rgba(0,0,0,.10) 0 3px, rgba(0,0,0,0) 3px 11px, rgba(255,255,255,.04) 11px 13px, rgba(0,0,0,0) 13px 26px),
    linear-gradient(90deg, var(--mahogany-dark) 0%, var(--mahogany) 30%, var(--mahogany-light) 55%, var(--mahogany) 80%, var(--mahogany-dark) 100%);
  font-family:'Oswald',sans-serif;
  color:var(--ink);
}
.parchment{position:absolute;left:0;top:0;width:850px;height:1200px}
.section-title{
  position:absolute;
  font-family:'Playfair Display SC',serif;font-weight:700;
  font-size:38px;line-height:38px;color:var(--ink);letter-spacing:.5px;
  text-transform:uppercase;
}
.section-note{
  position:absolute;font-family:'Michroma',sans-serif;font-size:6.4px;
  line-height:10px;text-transform:uppercase;color:var(--ink);
}
.item{position:absolute}
.item h3{
  font-weight:300;font-size:16.5px;line-height:18px;text-transform:uppercase;
  color:var(--ink);letter-spacing:-.1px;
}
.item p{
  font-weight:300;font-size:8.6px;line-height:12px;text-transform:uppercase;
  color:var(--ink-soft);
}
.item .price{
  font-family:'Michroma',sans-serif;font-size:6.4px;line-height:8px;color:var(--ink);
}
.col-left{width:320px}
.col-right{width:332px}
.narrow{width:180px}
.narrow-parm{width:160px}
.feature-photo{position:absolute;border-radius:50%;border:2px solid var(--ink)}
.photo-burger{left:614px;top:252px;width:142px;height:142px;
  background:radial-gradient(circle at 45% 35%, #d9a65a 0 22%, #b2692a 40%, #8a4a1c 70%, #f4f0e6 100%)}
.photo-lasagna{left:590px;top:648px;width:166px;height:166px;border:none;
  background:radial-gradient(circle at 50% 40%, #f2d34c 0 35%, #c89a2e 60%, #9b5a2a 85%, #2a1a10 100%)}
.divider{position:absolute;height:1px;background:var(--ink)}
.divider-knot{position:absolute;width:14px;height:14px;border:1.5px solid var(--ink);border-radius:50%;background:var(--paper)}
.footer{position:absolute;top:1024px;left:192px;display:flex;align-items:center;font-family:'Michroma',sans-serif;font-size:7px;letter-spacing:.6px;text-transform:uppercase;color:var(--ink)}
.footer .mark{width:16px;height:16px;background:var(--ink);display:inline-block;margin-right:14px}
.footer .link{margin-right:26px}
.split-note{position:absolute;top:1151px;left:0;width:850px;text-align:center;font-family:'Michroma',sans-serif;font-size:6.2px;letter-spacing:.3px;text-transform:uppercase;color:var(--white)}
</style>
</head>
<body>

<svg class="parchment" viewBox="0 0 850 1200" aria-hidden="true">
  <defs>
    <radialGradient id="paperTone" cx="50%" cy="45%" r="65%">
      <stop offset="0%" stop-color="#efe0bd"/>
      <stop offset="70%" stop-color="#e2c99a"/>
      <stop offset="100%" stop-color="#c49a5e"/>
    </radialGradient>
  </defs>
  <polygon fill="url(#paperTone)" stroke="#a8783e" stroke-width="1.5"
    points="80,98 130,84 190,92 245,80 300,90 360,78 420,88 470,80 530,92 590,82 650,94 700,86 760,100 792,104 800,150 790,210 802,270 792,330 806,380 798,440 806,500 796,560 804,620 794,680 802,740 790,800 800,860 792,920 802,980 794,1040 800,1090 760,1104 700,1096 640,1108 580,1098 520,1106 460,1096 400,1104 340,1096 280,1108 220,1096 160,1104 110,1094 66,1100 58,1050 66,990 54,930 64,870 56,810 68,750 56,690 66,630 54,560 64,500 52,440 62,380 52,320 64,260 54,200 64,140 56,104"/>
</svg>

<!-- Burgers -->
<h2 class="section-title" style="left:94px;top:146px">Burgers</h2>
<div class="section-note" style="left:94px;top:182px">All burgergs and sandwiches<br>served with your choice of potato</div>

<div class="item col-left" style="left:98px;top:209px">
  <h3>Black Angus Blue Cheese &amp; Bacon Burger</h3>
  <p>A juicy half pound burger with crumbled blue cheese and crisp bacon served on a toasted bun with lettuce, tomatoes, red onions and pickles.</p>
  <div class="price">8.99</div>
</div>
<div class="item col-left" style="left:98px;top:265px">
  <h3>All-American Cheeseburger</h3>
  <p>A half pound classic cheeseburger.</p>
  <div class="price">7.99</div>
</div>
<div class="item col-left" style="left:98px;top:309px">
  <h3>San Francisco Burger</h3>
  <p>A half pound burger topped with provolone cheese, crisp bacon, grilled onions, guacamole, mushrooms and black olives.</p>
  <div class="price">8.99</div>
</div>
<div class="item col-left" style="left:98px;top:365px">
  <h3>French Dip Burger</h3>
  <p>A half pound burger topped with swiss cheese and smothered in grilled onions. Served on a ciabatta bun with a side of french onion soup.</p>
  <div class="price">8.99</div>
</div>
<div class="item col-left" style="left:98px;top:421px">
  <h3>Gourmet Patty Melt</h3>
  <p>A half pound all beef patty stacked high with swiss cheese, grilled onions, and tomato! Served open faced on toasted rye.</p>
  <div class="price">7.99</div>
</div>

<div class="item col-right" style="left:427px;top:209px">
  <h3>Harrow Double Bacon Cheeseburger</h3>
  <p>Two mouth watering half pound patties layered with crisp bacon, american cheese, lettuce, tomatoes, red onions, and pickles.</p>
  <div class="price">9.99</div>
</div>
<div class="item narrow" style="left:427px;top:265px">
  <h3>Quesadilla Burger</h3>
  <p>A crispy flour tortilla stuffed with ground beef, jack and cheddar cheese, barbeque sauce, grilled peppers and onions, topped with lettuce pickles and red onions.</p>
  <div class="price">9.99</div>
</div>
<div class="item narrow" style="left:427px;top:345px">
  <h3>Pepper Jack Cheeseburger</h3>
  <p>A half pound burger topped with pepper jack cheese, grilled jalapeños and bacon.</p>
  <div class="price">8.99</div>
</div>
<div class="item col-right" style="left:427px;top:401px">
  <h3>Texas Burger</h3>
  <p>A half pounder decked out with american cheese, tangy barbecue sauce and crispy onion rings.</p>
  <div class="price">8.99</div>
</div>
<div class="item col-right" style="left:427px;top:457px">
  <h3>Bourbon Burger</h3>
  <p>A half pounder smothered in pepper jack cheese, bourbon glaze, and blooming onion petals.</p>
  <div class="price">8.99</div>
</div>

<div class="feature-photo photo-burger" role="img" aria-label="Photo of a burger with curly fries"></div>

<div class="divider" style="left:200px;top:533px;width:448px"></div>
<div class="divider-knot" style="left:417px;top:526px"></div>

<!-- Pasta -->
<h2 class="section-title" style="left:94px;top:562px">Pasta</h2>

<div class="item col-left" style="left:98px;top:609px">
  <h3>Lasagna</h3>
  <p>Harrow famous homemade lasagna!</p>
  <div class="price">SMALL 7.99 / LARGE 9.99</div>
</div>
<div class="item col-left" style="left:98px;top:653px">
  <h3>Italian Spaghetti &amp; Meatballs</h3>
  <p>This classic is topped with shredded parmesan cheese.</p>
  <div class="price">SMALL 6.99 / LARGE 8.99</div>
</div>
<div class="item col-right" style="left:427px;top:609px">
  <h3>Fettuccini Alfredo</h3>
  <p>Fettuccini topped with creamy alfredo and blended normandy vegetables served with your choice of chicken or grilled shrimp.</p>
  <div class="price">SMALL 7.99 / LARGE 9.99</div>
</div>
<div class="item narrow-parm" style="left:427px;top:664px">
  <h3>Chicken Parmesan</h3>
  <p>Tender grilled chicken breast topped with marinara sauce and parmesan cheese served on a bed of spaghetti</p>
  <div class="price">SMALL 7.99 / LARGE 9.99</div>
</div>

<div class="divider" style="left:192px;top:756px;width:398px"></div>
<div class="divider-knot" style="left:412px;top:749px"></div>

<div class="feature-photo photo-lasagna" role="img" aria-label="Photo of a slice of lasagna with melted cheese"></div>

<!-- Mexican -->
<h2 class="section-title" style="left:88px;top:785px">Mexican</h2>

<div class="item col-left" style="left:94px;top:831px">
  <h3>Taco Bowl</h3>
  <p>Your choice of chicken or beef in a fried 12 inch tortilla bowl, topped with lettuce, jack and cheddar cheese, tomatoes and sour cream.</p>
  <div class="price">8.99</div>
</div>
<div class="item col-left" style="left:94px;top:887px">
  <h3>Six Pack Tacos</h3>
  <p>Six crispy tacos stuffed with beef, cheese, lettuce and tomatoes.</p>
  <div class="price">8.99</div>
</div>
<div class="item col-left" style="left:94px;top:931px">
  <h3>Chimichanga</h3>
  <p>A 12 inch flour tortilla deep fried and stuffed with your choice of chicken or beef and jack and cheddar cheese. Smothered in melted jack cheese, lettuce, and tomatoes.</p>
  <div class="price">8.99</div>
</div>
<div class="item col-right" style="left:422px;top:831px;width:335px">
  <h3>Southwest Chicken Sancho</h3>
  <p>A bend of grilled chicken, cheese, lettuce, and salsa. Wrapped in a tortilla and smothered with creamy alfredo sauce, jack and cheddar cheese and tomatoes.</p>
  <div class="price">8.99</div>
</div>
<div class="item col-right" style="left:422px;top:887px;width:335px">
  <h3>Loaded Chicken Quesadilla</h3>
  <p>12 inch flour tortilla loaded with grilled chicken, barbecue sauce, crisp bacon and grilled onions and peppers.</p>
  <div class="price">9.99</div>
</div>

<!-- Footer -->
<div class="footer">
  <span class="mark"></span><span class="link">harrowtavernandgrille</span>
  <span class="mark"></span><span class="link">harrowtavernco.example</span>
  <span class="mark"></span><span class="link">Brewvoke</span>
</div>

<div class="split-note">When splitting a large portion, you will be charged the price of a small portion if a small portion is offered</div>

</body>
</html>
```